Seeking funky, innovative business cards

I am looking to refresh our current business cards to something more engaging, visual and impactful. We are a management consultancy firm, see website (www.larkstone-partners.com.au). I've included our colour scheme, sample of the slides we use and our old business cards. We would like our cards to have icons. The card should display:- Name- Title- Mobile number- Address- Email address- Website - Company logo- Our purpose statement "we help teams build workplaces they love"

Contact Information for Business Card

Brennan Ulfsson
Consultant
0468 927 341
Level 3, 218 Wexley Street, Melbourne 3000
brennan@larkstone-partners.com.au
www.larkstone-partners.com.au

Purpose statement "we help teams build workplaces they love"
LOGO available in google images

Font styles to use
Other font styles liked:
• Open Sans Light, Bebas Neue (open to other cool foints)

Colors
ffc214
5c5c5c
f5f5f5
fefefe

Requirements
Must have
• - Name
• - Title
• - Mobile number
• - Address
• - Email address
• - Website
• - Company logo
• - Our purpose statement "we help teams build workplaces they love"
Nice to have
• - Icons
• - Colour (see our colour scheme"

```html
<!DOCTYPE html>
<html lang="en">
<head>
<meta charset="utf-8">
<title>Larkstone Partners – Business Card</title>
<link rel="stylesheet" href="https://fonts.googleapis.com/css2?family=Open+Sans:ital,wght@0,400;0,600;1,400&display=swap">
<style>
  :root {
    --page-bg: #e7e3de;
    --card-top: #fefefe;
    --card-bottom: #f1efed;
    --ink: #1e1e1e;
    --accent: #e8a31a;
    --brand-dot: #f08a1c;
    --band-top: #3a3330;
    --band-bottom: #1c1c1c;
    --band-warm: #e0892a;
    --tagline: #c9b7a6;
  }
  * { margin: 0; padding: 0; box-sizing: border-box; }
  html, body {
    width: 1200px; height: 970px; overflow: hidden;
    background: var(--page-bg);
    font-family: "Open Sans", Arial, sans-serif;
  }
  .card {
    position: absolute; left: 80px; top: 190px;
    width: 1040px; height: 590px;
    border-radius: 24px; overflow: hidden;
    background: linear-gradient(180deg, var(--card-top), var(--card-bottom));
    box-shadow: 0 14px 40px rgba(0,0,0,.18);
  }
  .footer-band {
    position: absolute; left: 0; right: 0; bottom: 0; height: 160px;
    background: linear-gradient(180deg, var(--band-warm) 0%, var(--band-top) 28%, var(--band-bottom) 100%);
  }
  .brand {
    position: absolute; left: 58px; top: 142px;
    display: flex; align-items: center; gap: 18px;
  }
  .brand-dot {
    width: 26px; height: 26px; border-radius: 50%;
    background: var(--brand-dot);
  }
  .brand-name {
    font-weight: 400; color: #2b2b2b;
    font-size: 84px; line-height: 1; letter-spacing: -1px;
  }
  .contact {
    position: absolute; right: 68px; top: 76px;
    text-align: right; color: var(--ink);
  }
  .person-name { font-size: 37px; font-weight: 600; line-height: 1.1; }
  .person-title { font-size: 25px; color: var(--accent); line-height: 1.1; }
  .address { margin-top: 38px; font-size: 24px; line-height: 34px; }
  .lines { margin-top: 22px; list-style: none; }
  .lines li {
    display: flex; justify-content: flex-end; align-items: center;
    gap: 14px; font-size: 24px; line-height: 34px;
  }
  .icon {
    width: 28px; height: 28px; border-radius: 50%;
    background: var(--accent); flex: none;
    display: flex; align-items: center; justify-content: center;
  }
  .icon svg { width: 16px; height: 16px; }
  .tagline {
    position: absolute; right: 72px; top: 506px;
    font-style: italic; font-size: 24px; color: var(--tagline);
    letter-spacing: .3px;
  }
</style>
</head>
<body>
  <div class="card">
    <div class="footer-band" role="img" aria-label="Decorative orange and charcoal wave band"></div>

    <div class="brand">
      <span class="brand-dot"></span>
      <span class="brand-name">Larkstone</span>
    </div>

    <div class="contact">
      <div class="person-name">Brennan Ulfsson</div>
      <div class="person-title">Consultant</div>
      <div class="address">Level 3, 218 Wexley Street<br>Melbourne 3000</div>
      <ul class="lines">
        <li>0468 927 341
          <span class="icon"><svg viewBox="0 0 16 16"><path d="M4 1.5l2.2 3-1.3 1.4c.8 1.9 2.2 3.4 4.2 4.3l1.4-1.3 3 2.2-1.3 2.6C7.2 13.4 2.6 8.8 1.4 2.8z" fill="#fff"/></svg></span>
        </li>
        <li>brennan@larkstone-partners.com.au
          <span class="icon"><svg viewBox="0 0 16 16"><rect x="2" y="4" width="12" height="8.5" rx="1" fill="none" stroke="#fff" stroke-width="1.5"/><path d="M2.5 4.5L8 9l5.5-4.5" fill="none" stroke="#fff" stroke-width="1.5"/></svg></span>
        </li>
        <li>www.larkstone-partners.com.au
          <span class="icon"><svg viewBox="0 0 16 16"><circle cx="8" cy="8" r="6" fill="none" stroke="#fff" stroke-width="1.3"/><ellipse cx="8" cy="8" rx="2.6" ry="6" fill="none" stroke="#fff" stroke-width="1.1"/><path d="M2 8h12M3 5h10M3 11h10" stroke="#fff" stroke-width="1"/></svg></span>
        </li>
      </ul>
    </div>

    <p class="tagline">we help teams build workplaces they love</p>
  </div>
</body>
</html>
```